Velvet Lantern rebranding my business with a new business card

I have my new logo and now I need a refresher on my business cards. I really want something fun and fresh. I like black background or anything to make the color pop.
Logo
Name: Velvet Lantern
Contact Info as stated below:
Mira Pellow
555-013-4762
Logo
Name: Velvet Lantern
Mira Pellow
555-013-4762
fb.me/VelvetLanternbyMira
Instagram: @VelvetLanternbyMira

Industry/Entity Type

Business

Contact Information for Business Card

double-sided. Logo on one side. Contact info on the other.

Requirements
Must have
• Logo
• Name: Velvet Lantern
• Contact Info as stated below:
• Mira Pellow
• 555-013-4762
• fb.me/VelvetLanternbyMira
• fb.me/VelvetLanternbyMira

```html
<!DOCTYPE html>
<html lang="en">
<head>
<meta charset="utf-8">
<title>Velvet Lantern — Business Card</title>
<link href="https://fonts.googleapis.com/css2?family=Open+Sans:wght@400;600&display=swap" rel="stylesheet">
<style>
  :root {
    --backdrop: #2b2b2b;
    --card: #1f1f21;
    --card-edge: #2a2a2c;
    --ink: #e4e0e2;
    --ink-soft: #cfc9cc;
    --accent: #c58ea3;
    --ghost: rgba(255,255,255,0.045);
    --emboss: #343436;
  }
  * { box-sizing: border-box; margin: 0; padding: 0; }
  html, body {
    width: 1200px; height: 716px; overflow: hidden;
    background: var(--backdrop);
    font-family: "Open Sans", Arial, sans-serif;
  }
  .stage {
    position: relative; width: 1200px; height: 716px;
    display: flex; align-items: center; justify-content: center; gap: 60px;
  }
  .card {
    position: relative; width: 520px; height: 300px;
    background: var(--card);
    border: 1px solid var(--card-edge);
    border-radius: 22px; overflow: hidden;
  }
  /* front */
  .card--front { display: flex; align-items: center; justify-content: center; }
  .brand-mark {
    display: flex; align-items: center; gap: 14px;
    color: var(--emboss); font-weight: 600; font-size: 34px; letter-spacing: 1px;
  }
  .brand-mark__dot {
    width: 34px; height: 34px; border-radius: 50%; background: var(--emboss);
  }
  /* back */
  .ghost-name {
    position: absolute; left: 30px; top: 40px;
    font-size: 34px; font-weight: 600; color: var(--ghost); letter-spacing: 1px;
    white-space: nowrap;
  }
  .logo-badge {
    position: absolute; right: 30px; top: 66px;
    width: 130px; height: 130px; border-radius: 50%;
    border: 2px solid var(--accent);
    display: flex; align-items: center; justify-content: center; text-align: center;
    color: var(--ink); font-size: 17px; font-weight: 600; line-height: 1.2;
  }
  .holder-name {
    position: absolute; left: 26px; top: 164px;
    font-size: 24px; font-weight: 400; color: var(--ink);
  }
  .rule {
    position: absolute; left: 26px; right: 26px; top: 208px;
    height: 2px; background: var(--accent);
  }
  .contact-row {
    position: absolute; left: 26px; right: 26px; top: 226px;
    display: flex; align-items: center; justify-content: space-between;
    font-size: 11.5px; color: var(--ink-soft); white-space: nowrap;
  }
  .contact-row .sep { color: var(--ink-soft); }
  .contact-item { display: flex; align-items: center; gap: 5px; }
  .contact-item svg { width: 11px; height: 11px; fill: var(--accent); flex: none; }
  .plain-square { width: 10px; height: 10px; background: var(--accent); border-radius: 2px; }
</style>
</head>
<body>
<main class="stage">
  <section class="card card--front" aria-label="Card front">
    <div class="brand-mark"><span class="brand-mark__dot"></span>Velvet Lantern</div>
  </section>

  <section class="card card--back" aria-label="Card back">
    <div class="ghost-name" aria-hidden="true">Velvet Lantern</div>
    <div class="logo-badge">Velvet<br>Lantern</div>
    <h1 class="holder-name">Mira Pellow</h1>
    <div class="rule"></div>
    <div class="contact-row">
      <span class="contact-item">
        <svg viewBox="0 0 24 24" aria-hidden="true"><path d="M6.6 10.8a15.1 15.1 0 0 0 6.6 6.6l2.2-2.2a1 1 0 0 1 1-.25 11.4 11.4 0 0 0 3.6.57 1 1 0 0 1 1 1V20a1 1 0 0 1-1 1A17 17 0 0 1 3 4a1 1 0 0 1 1-1h3.5a1 1 0 0 1 1 1c0 1.25.2 2.45.57 3.57a1 1 0 0 1-.25 1z"/></svg>
        555-013-4762
      </span>
      <span class="sep">|</span>
      <span class="contact-item"><span class="plain-square"></span>fb.me/VelvetLanternbyMira</span>
      <span class="sep">|</span>
      <span class="contact-item">
        <svg viewBox="0 0 24 24" aria-hidden="true"><path d="M2 5h20v14H2z M4 7v.5l8 5 8-5V7l-8 5z" fill-rule="evenodd"/></svg>
        hello@velvetlantern.test
      </span>
    </div>
  </section>
</main>
</body>
</html>
```